Need help in designing new business card utilizing our new logo.

BuildMark Solutions works with Construction Business Owners, Managers & IT Professionals to strengthen software usage and increase user productivity.

Our Construction Accounting and Mobile Field Management Software Clients engage with us in the following areas:

New Software Implementations
Software Re-Implementations
Redesigning Software Usage at the User Level
Project Coordination & Management
Continued Software Support

Old tag line:
Clear Choices - Working Systems Built Right

www.buildmark-solutions.example

Ridge 4 is a product, but not needed for a new business card.

```html
<!DOCTYPE html>
<html lang="en">
<head>
<meta charset="utf-8">
<title>BuildMark Solutions — Business Card</title>
<link href="https://fonts.googleapis.com/css2?family=Roboto:wght@400;500;700&family=Roboto+Condensed:wght@700&display=swap" rel="stylesheet">
<style>
  :root {
    --brand-blue: #0b149f;
    --brand-blue-deep: #07108a;
    --silver-light: #d9d9d9;
    --silver-mid: #b9b9b9;
    --paper: #f3f3f3;
    --paper-shade: #e4e4e4;
    --ink: #1d1d1d;
    --ink-soft: #3a3a3a;
    --white: #ffffff;
    --backdrop: #bdbdbd;
  }
  * { box-sizing: border-box; margin: 0; padding: 0; }
  html, body { width: 1200px; height: 576px; overflow: hidden; }
  body {
    background: var(--backdrop);
    font-family: "Roboto", Arial, sans-serif;
    position: relative;
  }
  .card {
    position: absolute;
    width: 484px;
    height: 292px;
    border-radius: 14px;
    overflow: hidden;
    box-shadow: 0 4px 8px rgba(0,0,0,0.28);
  }

  /* Front */
  .card-front { left: 82px; top: 139px; background: var(--brand-blue); }
  .front-brand {
    position: absolute; top: 0; left: 0; right: 0; height: 165px;
    display: flex; align-items: center; justify-content: center; gap: 12px;
    background: linear-gradient(160deg, #0c18ad 0%, var(--brand-blue) 60%, var(--brand-blue-deep) 100%);
  }
  .brand-mark { width: 18px; height: 18px; background: var(--white); }
  .brand-name {
    font-weight: 500; font-size: 32px; letter-spacing: 0.5px; color: var(--white);
    white-space: nowrap;
  }
  .services-band {
    position: absolute; top: 165px; left: 0; right: 0; height: 82px;
    background: linear-gradient(180deg, var(--silver-light), var(--silver-mid));
    display: flex; flex-direction: column; align-items: center; justify-content: center;
    gap: 2px;
    font-size: 13px; color: var(--ink); line-height: 16px;
    white-space: nowrap;
  }
  .services-band .sep { padding: 0 8px; }
  .front-footer {
    position: absolute; bottom: 0; left: 0; right: 0; height: 45px;
    display: flex; align-items: center; justify-content: center; gap: 16px;
    color: var(--white); font-size: 12px; white-space: nowrap;
  }
  .front-footer .rule { width: 34px; height: 1px; background: rgba(255,255,255,0.7); }

  /* Back */
  .card-back {
    left: 602px; top: 138px;
    background: linear-gradient(135deg, var(--paper) 0%, #fafafa 45%, var(--paper-shade) 100%);
  }
  .back-brand {
    position: absolute; left: 28px; top: 120px;
    display: flex; align-items: center; gap: 8px;
  }
  .back-brand .brand-mark { width: 12px; height: 12px; background: var(--brand-blue); }
  .back-brand .brand-name { font-size: 19px; color: var(--brand-blue); letter-spacing: 0.2px; }
  .contact { position: absolute; left: 260px; top: 52px; right: 12px; color: var(--ink-soft); white-space: nowrap; }
  .person-name {
    font-family: "Roboto Condensed", "Arial Narrow", sans-serif;
    font-weight: 700; font-size: 22px; color: var(--brand-blue); line-height: 26px;
  }
  .person-role { font-size: 12px; margin-top: 2px; }
  .address { font-size: 12px; line-height: 17px; margin-top: 16px; }
  .contact-list { list-style: none; margin-top: 10px; font-size: 12px; line-height: 17px; }
  .contact-list li { display: flex; align-items: center; gap: 9px; }
  .contact-list svg { width: 10px; height: 10px; fill: var(--brand-blue); flex: none; }
  .tagline-band {
    position: absolute; bottom: 0; left: 0; right: 0; height: 29px;
    background: var(--brand-blue);
    display: flex; align-items: center; justify-content: center;
    color: var(--white); font-size: 12px; white-space: nowrap;
  }
</style>
</head>
<body>

<section class="card card-front">
  <div class="front-brand">
    <span class="brand-mark"></span>
    <span class="brand-name">BuildMark Solutions</span>
  </div>
  <div class="services-band">
    <p>New Software Implementations<span class="sep">|</span>Software Re-Implementations</p>
    <p>Redesigning Software Usage at the User Level</p>
    <p>Project Coordination &amp; Management<span class="sep">|</span>Continued Software Support</p>
  </div>
  <div class="front-footer">
    <span class="rule"></span>
    <span>www.buildmark-solutions.example</span>
    <span class="rule"></span>
  </div>
</section>

<section class="card card-back">
  <div class="back-brand">
    <span class="brand-mark"></span>
    <span class="brand-name">BuildMark Solutions</span>
  </div>
  <div class="contact">
    <h1 class="person-name">Dana R. Whitfield</h1>
    <p class="person-role">Owner</p>
    <p class="address">41B Harbor Lane - Suite 118<br>Millbrook, NY 12545</p>
    <ul class="contact-list">
      <li>
        <svg viewBox="0 0 10 10" aria-hidden="true"><rect x="2" y="0" width="6" height="10" rx="1"/><rect x="3" y="1.3" width="4" height="6" fill="#f3f3f3"/></svg>
        555-014-2287
      </li>
      <li>
        <svg viewBox="0 0 10 10" aria-hidden="true"><path d="M0 3 Q5 0 10 3 L9 4.5 L7 4 L7 3 Q5 2.3 3 3 L3 4 L1 4.5 Z"/><rect x="1.5" y="5" width="7" height="4.5" rx="0.8"/></svg>
        555-019-4400 ext. 100
      </li>
      <li>
        <svg viewBox="0 0 10 10" aria-hidden="true"><rect x="0" y="2" width="10" height="6.5"/><path d="M0.5 2.5 L5 6 L9.5 2.5" stroke="#f3f3f3" stroke-width="0.9" fill="none"/></svg>
        dana@buildmark-solutions.example
      </li>
      <li>
        <svg viewBox="0 0 10 10" aria-hidden="true"><circle cx="5" cy="5" r="5"/><path d="M0 5 H10 M5 0 V10 M5 0 Q2 5 5 10 M5 0 Q8 5 5 10" stroke="#f3f3f3" stroke-width="0.6" fill="none"/></svg>
        www.buildmark-solutions.example
      </li>
    </ul>
  </div>
  <div class="tagline-band">Clear Choices - Working Systems Built Right</div>
</section>

</body>
</html>
```